New Coffee Shop business card

We are opening our new coffee shop and are needing business cards to take with us on February 6th to Atlanta, Ga to a show.

We will be offering the following menu type items:

coffee
teas
espresso
frappes
smoothies

sandwiches
soups
salads
pastries
ice cream

Our shop is in a rural country-side area and we would like to convey that feel in our shop. In addition to the cafe we will also be selling gifts and furniture and other home decor. Much of this merchandise will be rescued, refurbished or repurposed which is also a core value of what we are all about.

We have a company logo we would like incorporated into the design.

We will also provide files that have the elements of the logo which may also be useful in the design of the card.

Since we are not open yet we need one slightly altered version of the card as well as the final product which states "Opening in the summer 2015"

Target Market(s)

moderate to slightly upscale and folksy.

Industry/Entity Type

Coffee Shop

Contact Information for Business Card

Fern Kettle Coffee
name
address
phone number
email

Card

Font styles to use
Sans Serif

Requirements
Must have
• Must include Logo
• Must include information on menu.
• Must include information on our merchandise sales as described inthe project description.
• Color scheme to complement the logo
Nice to have
• The following descriptions
• "We are also selling gifts, furniture, and other home decoration."
• "We rescue, refurbish, and repurpose old furniture so it can live again."

```html
<!DOCTYPE html>
<html lang="en">
<head>
<meta charset="utf-8">
<title>Fern Kettle Coffee – Business Cards</title>
<link href="https://fonts.googleapis.com/css2?family=Jost:wght@300;400;600;700&display=swap" rel="stylesheet">
<style>
  :root {
    --bg: #e9e6e1;
    --berry: #b8364b;
    --berry-light: #c9495d;
    --berry-dark: #9c2a3d;
    --slate: #3d3f44;
    --slate-dark: #2e3034;
    --paper: #ffffff;
    --paper-shade: #f1f0f0;
    --menu-text: #c56a7a;
    --ink-light: #f6f0f1;
  }
  * { box-sizing: border-box; margin: 0; padding: 0; }
  html, body { width: 1200px; height: 1000px; overflow: hidden; }
  body {
    background: var(--bg);
    font-family: "Jost", Arial, sans-serif;
    position: relative;
  }
  .card {
    position: absolute;
    width: 620px;
    height: 355px;
    border-radius: 4px;
    overflow: hidden;
    box-shadow: 0 10px 28px rgba(0,0,0,0.22);
  }

  /* ---------- Front card ---------- */
  .card-front { left: 80px; top: 90px; background: linear-gradient(135deg, var(--berry-light), var(--berry)); }
  .brand-panel {
    position: absolute; left: 0; top: 0; bottom: 0; width: 240px;
    background: linear-gradient(160deg, var(--slate), var(--slate-dark));
    display: flex; align-items: center; justify-content: center; gap: 12px;
    padding: 0 20px;
  }
  .brand-dot { width: 16px; height: 16px; border-radius: 50%; background: var(--paper); flex: none; }
  .brand-name { color: var(--paper); font-weight: 300; font-size: 32px; line-height: 1.05; }
  .contact {
    position: absolute; left: 268px; top: 38px; color: var(--paper);
  }
  .contact .shop { font-weight: 300; font-size: 20px; margin-bottom: 10px; }
  .contact .person { font-weight: 700; font-size: 25px; margin-bottom: 10px; }
  .contact .rule { width: 150px; height: 2px; background: var(--paper); margin-bottom: 22px; }
  .contact .line { font-weight: 300; font-size: 16px; margin-bottom: 16px; }
  .contact .line.gap { margin-bottom: 30px; }
  .cup-icon { position: absolute; right: 34px; top: 26px; width: 110px; height: 110px; }

  /* ---------- Back card ---------- */
  .card-back { left: 500px; top: 540px; background: linear-gradient(160deg, var(--paper), var(--paper-shade)); }
  .story-band {
    position: absolute; left: 0; top: 0; bottom: 0; width: 200px;
    background: linear-gradient(180deg, var(--berry-light), var(--berry-dark));
    border-right: 6px solid var(--paper);
    box-shadow: 3px 0 0 var(--berry);
    padding: 90px 16px 0 18px;
    color: var(--ink-light);
    font-size: 13.5px; line-height: 1.35; font-weight: 400;
  }
  .story-band p + p { margin-top: 10px; }
  .flourish { position: absolute; background: var(--berry); opacity: 0.35; border-radius: 40% 60% 50% 50%; }
  .flourish-band { left: 40px; top: 22px; width: 110px; height: 40px; background: var(--paper); opacity: 0.55; }
  .flourish-top { left: 218px; top: 10px; width: 90px; height: 26px; }
  .flourish-bottom { left: 218px; bottom: 10px; width: 90px; height: 26px; }
  .back-brand { position: absolute; left: 232px; top: 44px; display: flex; align-items: center; gap: 8px; color: var(--slate); font-size: 17px; font-weight: 400; }
  .back-brand .brand-dot { width: 10px; height: 10px; background: var(--slate); }
  .offer { position: absolute; left: 232px; top: 92px; color: var(--berry); }
  .offer h2 { font-weight: 400; font-size: 34px; line-height: 1; }
  .offer .lede { font-weight: 300; font-size: 19px; margin-top: 4px; }
  .menu { display: flex; gap: 48px; margin-top: 16px; list-style: none; }
  .menu ul { list-style: none; color: var(--menu-text); font-size: 18px; font-weight: 300; line-height: 1.2; }
  .opening {
    position: absolute; right: 26px; bottom: 22px; text-align: right;
    color: var(--berry); font-weight: 700; font-size: 19px; line-height: 1.15;
  }
</style>
</head>
<body>

  <section class="card card-front" aria-label="Business card front">
    <div class="brand-panel">
      <span class="brand-dot"></span>
      <span class="brand-name">Fern Kettle<br>Coffee</span>
    </div>
    <div class="contact">
      <p class="shop">Fern Kettle</p>
      <p class="person">John Doe</p>
      <div class="rule"></div>
      <p class="line gap">Address:</p>
      <p class="line">phone: 123 456 7890</p>
      <p class="line">email: yourname@domaine.com</p>
      <p class="line">Card:</p>
    </div>
    <svg class="cup-icon" viewBox="0 0 110 110" aria-hidden="true">
      <g fill="none" stroke="#fff" stroke-width="3" stroke-linecap="round">
        <path d="M28 48 C14 38 30 26 22 14"/>
        <path d="M42 48 C30 36 48 24 38 8"/>
      </g>
      <path d="M52 50 H92 V62 C92 80 80 90 70 90 C60 90 52 80 52 62 Z" fill="#fff"/>
      <path d="M92 56 C104 56 104 72 90 74" fill="none" stroke="#fff" stroke-width="4"/>
      <rect x="40" y="94" width="66" height="4" rx="2" fill="#fff"/>
    </svg>
  </section>

  <section class="card card-back" aria-label="Business card back">
    <div class="story-band">
      <div class="flourish flourish-band" role="img" aria-label="Decorative floral flourish"></div>
      <p>We are also selling gifts, furniture, and other home decoration.</p>
      <p>We rescue, refurbish, and repurpose old furniture so it can live again.</p>
    </div>
    <div class="flourish flourish-top" role="img" aria-label="Decorative floral flourish"></div>
    <div class="flourish flourish-bottom" role="img" aria-label="Decorative floral flourish"></div>

    <div class="back-brand"><span class="brand-dot"></span>Fern Kettle</div>

    <div class="offer">
      <h2>coffee shop</h2>
      <p class="lede">stuff we’re selling...</p>
      <div class="menu">
        <ul>
          <li>coffee</li><li>teas</li><li>espresso</li><li>frappes</li><li>smoothies</li>
        </ul>
        <ul>
          <li>sandwiches</li><li>soups</li><li>salads</li><li>pastries</li><li>ice cream</li>
        </ul>
      </div>
    </div>

    <p class="opening">Opening<br>in the<br>summer<br>2015</p>
  </section>

</body>
</html>
```